Health Coaching website focused on diabetes management using Vantelo template

I am starting a health coaching business and would like to use Plumestack and an Vantelo template. The coaching will focus on Pre-diabetic and chronic disease patients so it will need to have a personal as well as a slight clinical look to it. The site should have an overall look similar to Meadow Loop theme. I will purchase the Vantelo designer package for use.

Target Market(s)

40-60 year olds with pre-diabetes or concerned about chronic disease, maintaining health, nutrition and weight loss

Industry/Entity Type

Health And Wellness

Number of Pages Required

5+ page

Colors
87cfc6
60b9df
fee18a
00a990
3276b5

Requirements
Must have
• It should contain an ecommerce tab, member's only area, interactive blog, built-in SEO and an opt-in area on every page. It should have several call to actions throughout the site. The site should have an overall look similar to Meadow Loop theme. Hosting on Servunda. Also needed all the essential plumestack plugins:
• Keystep forms & Keystep entry pages
• Pondra Metrics
• Vantelo shield plus
• Postwren
• Valdeno
• Vault Parrot
• Kindle SEO
• Drifting Share Strip
• Q7 Rapid Store
• Tembi
Nice to have
• Ecommerce ready with cartoflex plugin
• Hi-res pictures of people in my demographic enjoying life and/or exercising, cooking, etc.
Should not have
• slider on homepage
• my profile on homepage

```html
<!DOCTYPE html>
<html lang="en">
<head>
<meta charset="utf-8">
<title>Brightwell Living — Health Coaching</title>
<link href="https://fonts.googleapis.com/css2?family=Open+Sans:wght@300;400;600;700&display=swap" rel="stylesheet">
<style>
:root{
  --navy:#3276b5;
  --sky:#60b9df;
  --teal:#87cfc6;
  --green:#00a990;
  --butter:#fee18a;
  --cream:#fbf4dc;
  --ink:#3a3f44;
  --muted:#7d858c;
  --line:#e1e4e6;
  --mist:#f1f2f3;
  --footer:#1e2830;
  --footer-deep:#141b21;
  --white:#ffffff;
}
*{box-sizing:border-box;margin:0;padding:0}
html,body{width:1200px;height:3288px;overflow:hidden}
body{font-family:"Open Sans",Arial,sans-serif;color:var(--ink);background:var(--white);font-size:13px;line-height:1.6}
.wrap{width:900px;margin:0 auto;position:relative}
.btn{display:inline-block;background:var(--green);color:var(--white);font-size:11px;font-weight:600;text-transform:uppercase;letter-spacing:.5px;padding:8px 20px;border-radius:2px}
.section-title{text-align:center;font-size:30px;font-weight:400;color:var(--ink)}
.section-title span{color:var(--navy);font-weight:600}
.title-rule{width:340px;height:1px;background:var(--line);margin:12px auto 0;position:relative}
.title-rule::after{content:"";position:absolute;left:50%;top:-1px;width:40px;height:3px;margin-left:-20px;background:var(--green)}

/* header */
.site-header{height:112px}
.site-header .wrap{height:112px;display:flex;align-items:center;justify-content:space-between}
.brand{display:flex;align-items:center;gap:14px}
.brand-dot{width:46px;height:46px;border-radius:50%;background:var(--teal)}
.brand-name{font-size:26px;font-weight:600;color:var(--navy);line-height:1.05;width:170px}
.header-actions{display:flex;align-items:center;gap:22px}
.phone{display:flex;align-items:center;gap:10px;font-size:17px;color:var(--ink)}
.phone-icon{width:34px;height:34px;border-radius:50%;background:var(--green);display:flex;align-items:center;justify-content:center}
.appointment{background:var(--green);color:var(--white);font-size:12px;font-weight:600;text-transform:uppercase;padding:10px 16px;display:flex;align-items:center;gap:8px}

/* nav */
.main-nav{height:36px;background:var(--navy)}
.main-nav ul{list-style:none;display:flex;height:36px}
.main-nav li{color:var(--white);font-size:11px;font-weight:600;text-transform:uppercase;padding:0 17px;line-height:36px}
.main-nav li.active{background:var(--green)}

/* hero */
.hero{height:484px;position:relative;background:linear-gradient(100deg,#6b4a33 0%,#b98a5e 30%,#d9c3a4 55%,#8f7766 80%,#5c4a40 100%)}
.hero-copy{position:absolute;left:740px;top:150px;width:300px;color:var(--white);text-align:center}
.hero-copy h1{font-size:40px;font-weight:600;line-height:1.15;text-shadow:0 1px 4px rgba(0,0,0,.3)}
.hero-copy p{font-size:12px;margin:14px 0 16px;opacity:.95}

/* about */
.about{height:328px}
.about .wrap{display:flex;justify-content:space-between;padding-top:34px}
.about-text{width:590px}
.about-text h2{font-size:28px;font-weight:400;display:flex;align-items:center;gap:10px}
.about-text h2 span{color:var(--navy);font-weight:600}
.about-text h2 .ico{width:34px;height:34px;border-radius:50%;background:var(--teal)}
.about-text .lead{font-size:14px;margin:22px 0 14px}
.about-text .lead b{color:var(--navy);font-weight:600}
.about-text p{color:var(--muted);font-size:12.5px;margin-bottom:10px}
.consult{width:208px;border:1px solid var(--line)}
.consult h3{background:var(--navy);color:var(--white);font-size:15px;font-weight:600;text-align:center;padding:8px 0}
.consult form{padding:12px}
.field{border:1px solid var(--line);height:30px;font-size:11px;color:var(--muted);padding:6px 8px;margin-bottom:10px}
.field.tall{height:80px}
.consult .btn{display:block;text-align:center}

/* programs */
.programs{height:420px;background:var(--mist);padding-top:36px}
.program-grid{display:flex;justify-content:space-between;margin-top:40px}
.program{width:428px;height:212px;position:relative}
.program .pic{height:212px}
.pic-a{background:linear-gradient(135deg,#4a3a30,#b48a6e 55%,#d9d3cc)}
.pic-b{background:linear-gradient(135deg,#eef1ef,#c9d8c0 45%,#cf5a4a 75%,#e8e4de)}
.program-label{position:absolute;left:0;right:0;bottom:0;height:36px;background:var(--green);color:var(--white);font-size:12px;font-weight:600;text-transform:uppercase;padding:0 14px;display:flex;align-items:center;justify-content:space-between}
.program-label b{font-size:22px;font-weight:400}

/* blog + connections */
.stories{height:540px;padding-top:110px}
.stories .wrap{display:flex;justify-content:space-between}
.col{width:428px}
.col-head{display:flex;justify-content:space-between;align-items:center;border-bottom:1px solid var(--line);padding-bottom:10px;margin-bottom:20px}
.col-head h2{font-size:26px;font-weight:400}
.col-head h2 span{color:var(--navy);font-weight:600}
.arrows{display:flex;gap:3px}
.arrows i{width:20px;height:20px;background:var(--line);display:block}
.post{display:flex;gap:16px;margin-bottom:20px}
.post .thumb{width:96px;height:80px;flex:none}
.t1{background:linear-gradient(135deg,#a67b5b,#e0c2a2)}
.t2{background:linear-gradient(135deg,#6f8fa9,#d8c1a8)}
.t3{background:linear-gradient(135deg,#8a4f3a,#d9a07a)}
.post h4{font-size:13px;font-weight:700;color:var(--ink)}
.post p{font-size:11.5px;color:var(--muted);line-height:1.5}
.post .more{color:var(--green);font-size:11px}
.video{height:300px;position:relative;background:linear-gradient(135deg,#e8eef3,#c4d3de 50%,#d8a6a8)}
.video-bar{position:absolute;left:0;right:0;bottom:0;height:26px;background:rgba(20,30,40,.75);display:flex;align-items:center;padding:0 10px;gap:10px}
.video-bar .track{flex:1;height:3px;background:rgba(255,255,255,.4)}
.play{position:absolute;left:50%;top:50%;width:56px;height:56px;margin:-28px 0 0 -28px;border-radius:50%;background:rgba(255,255,255,.85);display:flex;align-items:center;justify-content:center}

/* signup */
.signup{height:300px;background:linear-gradient(90deg,var(--navy),#3f86c3 50%,var(--navy));position:relative;color:var(--white);text-align:center;padding-top:62px}
.signup h2{font-size:30px;font-weight:400}
.signup .title-rule{background:rgba(255,255,255,.35)}
.signup .title-rule::after{background:var(--white)}
.signup-form{display:flex;justify-content:center;margin-top:44px}
.signup-form .input{width:470px;height:34px;background:var(--white);color:var(--muted);font-size:12px;text-align:left;padding:8px 12px}
.signup-form .btn{height:34px;padding:9px 26px;border-radius:0}
.plane{position:absolute;left:380px;top:40px}

/* testimonials */
.testimonials{height:340px;padding-top:56px}
.testimonial-grid{display:flex;justify-content:space-between;margin-top:44px}
.testimonial{width:436px;display:flex;gap:18px}
.avatar{width:100px;height:100px;border-radius:50%;border:4px solid var(--teal);flex:none;background:linear-gradient(135deg,#c9a58a,#7b6a5e)}
.testimonial p{font-size:11.5px;color:var(--muted);line-height:1.55}
.testimonial .who{margin-top:10px;font-size:11px;color:var(--ink)}
.testimonial .who span{color:var(--sky)}

/* profile */
.profile{height:400px;background:var(--cream);padding-top:44px}
.profile .row{display:flex;gap:50px;margin-top:36px}
.portrait{width:260px;height:260px;border-radius:50%;flex:none;margin-top:-10px;border:6px solid var(--white);background:linear-gradient(135deg,#e9e2d8,#bfd6dc 55%,#8fb7c4)}
.profile-text .lead{font-size:14px;color:var(--navy);margin-bottom:12px}
.profile-text p{font-size:12.5px;color:var(--muted);margin-bottom:12px}

/* footer */
.site-footer{height:300px;background:var(--footer);color:#b9c1c7;padding-top:30px}
.site-footer .wrap{display:flex;gap:50px}
.site-footer h5{color:var(--white);font-size:14px;font-weight:700;text-transform:uppercase;margin-bottom:14px}
.site-footer h5 span{color:var(--green);font-weight:400}
.quick ul{list-style:none;font-size:12px;line-height:1.9}
.quick{width:120px}
.contact{width:220px;font-size:11.5px}
.contact .line{display:flex;gap:8px;align-items:center;margin-top:14px;color:var(--white)}
.map{width:220px;height:150px;background:linear-gradient(135deg,#e6e2d6,#cfd9c4 50%,#b9cfe0)}
.footer-mark{width:150px;height:150px;border-radius:50%;background:#2b3842;margin-top:20px}
.base{height:28px;background:var(--footer-deep);color:#8a949b;font-size:10.5px}
.base .wrap{display:flex;justify-content:space-between;align-items:center;height:28px}
.social{display:flex;gap:5px}
.social i{width:18px;height:18px;border-radius:50%;background:var(--navy);display:block}
</style>
</head>
<body>

<header class="site-header">
  <div class="wrap">
    <div class="brand">
      <span class="brand-dot"></span>
      <span class="brand-name">Brightwell Living</span>
    </div>
    <div class="header-actions">
      <div class="phone">
        <span class="phone-icon"><svg width="16" height="16" viewBox="0 0 24 24"><path fill="#fff" d="M6.6 10.8a15 15 0 0 0 6.6 6.6l2.2-2.2a1 1 0 0 1 1-.25 11.4 11.4 0 0 0 3.6.57 1 1 0 0 1 1 1V20a1 1 0 0 1-1 1A17 17 0 0 1 3 4a1 1 0 0 1 1-1h3.5a1 1 0 0 1 1 1c0 1.25.2 2.45.57 3.6a1 1 0 0 1-.25 1z"/></svg></span>
        123 456 7890
      </div>
      <div class="appointment">
        <svg width="14" height="14" viewBox="0 0 24 24"><rect x="3" y="5" width="18" height="16" rx="2" fill="none" stroke="#fff" stroke-width="2"/><path d="M3 10h18M8 3v4M16 3v4" stroke="#fff" stroke-width="2"/></svg>
        Make an appointment
      </div>
    </div>
  </div>
</header>

<nav class="main-nav">
  <div class="wrap">
    <ul>
      <li class="active">Home</li><li>My Profile</li><li>Our Courses</li><li>Special Offers</li><li>Testimonials</li><li>Blog</li><li>FAQ's</li><li>Contact Us</li>
    </ul>
  </div>
</nav>

<section class="hero" role="img" aria-label="Photo of a smiling couple in their fifties cooking a healthy meal together in a bright kitchen">
  <div class="hero-copy">
    <h1>Brightwell Living</h1>
    <p>Small daily choices add up to lasting health, energy and confidence at every age.</p>
    <span class="btn">Join us today</span>
  </div>
</section>

<section class="about">
  <div class="wrap">
    <div class="about-text">
      <h2><span class="ico"></span>About <span>Brightwell Living</span></h2>
      <div class="title-rule" style="margin:10px 0 0;width:100%"></div>
      <p class="lead">We walk with you toward <b>better blood sugar</b>, steady weight and a calmer, stronger body.</p>
      <p>Our coaching blends clinical knowledge with a personal touch. Together we build simple habits around food, movement, sleep and stress that fit your real life, so changes last long after our sessions end and you feel in charge of your own health again.</p>
      <p>Whether you were just told you are pre-diabetic or you live with a chronic condition, we meet you where you are and plan each step with care.</p>
      <span class="btn" style="margin-top:8px">Read more</span>
    </div>
    <aside class="consult">
      <h3>Free Consultation</h3>
      <form>
        <div class="field">Name</div>
        <div class="field">Email</div>
        <div class="field tall">Message</div>
        <span class="btn">Submit</span>
      </form>
    </aside>
  </div>
</section>

<section class="programs">
  <div class="wrap">
    <h2 class="section-title">Brightwell <span>Programs</span></h2>
    <div class="title-rule"></div>
    <div class="program-grid">
      <div class="program">
        <div class="pic pic-a" role="img" aria-label="Close-up photo of hands testing blood sugar with a glucose meter"></div>
        <div class="program-label">Pre Diabetes &amp; Chronic Disease <b>+</b></div>
      </div>
      <div class="program">
        <div class="pic pic-b" role="img" aria-label="Photo of an apple and measuring tape on a plate beside a fork and knife"></div>
        <div class="program-label">Nutrition &amp; Weight Management <b>+</b></div>
      </div>
    </div>
  </div>
</section>

<section class="stories">
  <div class="wrap">
    <div class="col">
      <div class="col-head">
        <h2>Latest <span>Blog</span></h2>
        <div class="arrows"><i></i><i></i></div>
      </div>
      <div class="post">
        <div class="thumb t1" role="img" aria-label="Photo of an older couple enjoying a walk outdoors"></div>
        <div><h4>Moving More Each Day</h4><p>Short walks after meals can help steady blood sugar and lift your mood in a matter of weeks.</p><span class="more">Read more</span></div>
      </div>
      <div class="post">
        <div class="thumb t2" role="img" aria-label="Photo of a woman stretching in her living room"></div>
        <div><h4>Stretching For Comfort</h4><p>Gentle stretches ease stiff joints and help your body feel ready for the day ahead.</p><span class="more">Read more</span></div>
      </div>
      <div class="post">
        <div class="thumb t3" role="img" aria-label="Photo of a couple preparing vegetables together"></div>
        <div><h4>Smart Swaps In Kitchen</h4><p>Simple ingredient changes keep your favourite meals tasty while cutting sugar and salt.</p><span class="more">Read more</span></div>
      </div>
    </div>
    <div class="col">
      <div class="col-head">
        <h2>Brightwell <span>Connections</span></h2>
      </div>
      <div class="video" role="img" aria-label="Video still of a coach talking with a client at a kitchen table">
        <span class="play"><svg width="20" height="22" viewBox="0 0 20 22"><path d="M2 1l17 10L2 21z" fill="var(--navy)"/></svg></span>
        <div class="video-bar">
          <svg width="10" height="12" viewBox="0 0 10 12"><path d="M0 0l10 6-10 6z" fill="#fff"/></svg>
          <span class="track"></span>
          <svg width="12" height="12" viewBox="0 0 12 12"><path d="M0 4h3l4-4v12L3 8H0z" fill="#fff"/></svg>
        </div>
      </div>
    </div>
  </div>
</section>

<section class="signup">
  <svg class="plane" width="70" height="56" viewBox="0 0 70 56"><path d="M2 26L68 2 52 54 34 36z" fill="#fff"/><path d="M34 36L68 2 26 40l2 14z" fill="#d8e6f3"/></svg>
  <h2>Email Signup</h2>
  <div class="title-rule"></div>
  <div class="signup-form">
    <div class="input">Email</div>
    <span class="btn">Subscribe</span>
  </div>
</section>

<section class="testimonials">
  <div class="wrap">
    <h2 class="section-title">Clients <span>Testimonials</span></h2>
    <div class="title-rule"></div>
    <div class="testimonial-grid">
      <div class="testimonial">
        <div class="avatar" role="img" aria-label="Portrait photo of a client"></div>
        <div>
          <p>“Working with my coach changed how I shop, cook and move. My numbers are finally heading the right way and I have more energy for my grandchildren than I have had in years. Every session felt kind, clear and practical.”</p>
          <div class="who">- Mrs. Clara Dunmore <span>Brightwell</span></div>
        </div>
      </div>
      <div class="testimonial">
        <div class="avatar" role="img" aria-label="Portrait photo of a client"></div>
        <div>
          <p>“I was worried after my diagnosis, but the plan was simple to follow. I lost weight slowly and steadily, sleep better and feel in control again. I look forward to each check-in and the friendly support in between.”</p>
          <div class="who">- Mrs. Helen Ashby <span>Brightwell</span></div>
        </div>
      </div>
    </div>
  </div>
</section>

<section class="profile">
  <div class="wrap">
    <h2 class="section-title">My <span>Profile</span></h2>
    <div class="title-rule"></div>
    <div class="row">
      <div class="portrait" role="img" aria-label="Portrait photo of the health coach holding a green apple"></div>
      <div class="profile-text">
        <p class="lead">A certified health coach helping adults prevent diabetes and live well with chronic conditions.</p>
        <p>I spent many years in clinical settings before turning to coaching, where I could spend real time with each person. My approach mixes evidence based guidance on nutrition and activity with plenty of listening, encouragement and honest feedback along the way.</p>
        <p>Outside of work I love cooking seasonal food, long walks with my family and finding new ways to make healthy living feel joyful rather than strict.</p>
        <span class="btn">Read more</span>
      </div>
    </div>
  </div>
</section>

<footer class="site-footer">
  <div class="wrap">
    <div class="quick">
      <h5>Quick <span>Links</span></h5>
      <ul><li>Home</li><li>My Profile</li><li>Our Courses</li><li>Special Offers</li><li>Testimonials</li><li>Blog</li><li>FAQ's</li><li>Contact Us</li></ul>
    </div>
    <div class="contact">
      <h5>Contact <span>Details</span></h5>
      <div style="color:var(--white);font-weight:600">BRIGHTWELL LIVING</div>
      <div>214 Linden Grove Road, Suite 5</div>
      <div>Maple Ridge, OR 97100</div>
      <div class="line"><svg width="14" height="14" viewBox="0 0 24 24"><path fill="var(--green)" d="M6.6 10.8a15 15 0 0 0 6.6 6.6l2.2-2.2a1 1 0 0 1 1-.25 11.4 11.4 0 0 0 3.6.57 1 1 0 0 1 1 1V20a1 1 0 0 1-1 1A17 17 0 0 1 3 4a1 1 0 0 1 1-1h3.5a1 1 0 0 1 1 1c0 1.25.2 2.45.57 3.6a1 1 0 0 1-.25 1z"/></svg>123 456 7890</div>
      <div class="line"><svg width="14" height="12" viewBox="0 0 24 20"><rect x="1" y="1" width="22" height="18" rx="2" fill="none" stroke="var(--green)" stroke-width="2"/><path d="M1 2l11 9 11-9" fill="none" stroke="var(--green)" stroke-width="2"/></svg>hello@brightwellliving.com</div>
    </div>
    <div>
      <h5>Location <span>Map</span></h5>
      <div class="map" role="img" aria-label="Street map showing the office location"></div>
    </div>
    <div class="footer-mark"></div>
  </div>
</footer>
<div class="base">
  <div class="wrap">
    <span>© 2016 Brightwell Living. All Rights Reserved.</span>
    <div class="social"><i></i><i></i><i></i><i></i><i></i><i></i></div>
  </div>
</div>

</body>
</html>
```